Ridge Lass Crew (Flyer)

I want a flyer to advertise my service.
Details below, and logo's to use are attached.

A girls only after school program, 11-14yrs, as OSHC is no longer avail, dedicated to coaching & mentoring our girls into strong, independent young women.

The Brainchild of Rebecca Folwin, Ridge Lass Crew was created to address the growing demand for after school/school holiday supervision for kids moving from primary into high school, when OSHC ceases to exist.
With over 12 years experience mentoring and coaching young women in the corporate world, Bec decided to leave her role as a Director with Tarrant Trust, and follow her passion.
Bec, along with her sister Lorraine, who has over 10 years experience in local communities as a Youth Worker, and is also a qualified Enrolled Nurse, embarked on building a program designed to keep parents happy (by knowing their girls are safe) and dedicated to coaching and mentoring our girls into strong, independent young women.
Open every afternoon and during school holidays, we look to offer;
- Daily meditation
- Healthy snacks
- Dedicated homework time
- Organised group activity, led by qualified instructors (yoga, fitness class, soccer etc)
- Regular guests speakers, addressing issues/concerns for young people today
- SOCIAL MEDIA FREE ZONE

Located 87 Pelham Pde, Ashvale Heights (across from Crestmoor Day Clinic)
Open 3-6pm Monday to Friday

Facebook page: http://fb.example/ridgelasscrew
Email: info@ridgelasscrew.example.au
Mobile: 0455817396

Target Market(s)

Parents of teenage girls, teenage girls 11-14 years

Industry/Entity Type

School

Font styles to use
Sans Serif

Colors
b768aa
e667a6

Requirements
Must have
• What progam is - see brief
• Who runs it
Should not have
• Not be too busy, not overly mature images

```html
<!DOCTYPE html>
<html lang="en">
<head>
<meta charset="utf-8">
<title>Ridge Lass Crew – After School Program Flyer</title>
<link rel="stylesheet" href="https://fonts.googleapis.com/css2?family=Bebas+Neue&family=Cinzel:wght@700&family=Cookie&family=Cousine:wght@700&family=Montserrat:wght@700&family=Oswald:wght@300;400&family=Sofia&family=Sriracha&display=swap">
<style>
  :root {
    --pink: #e667a6;
    --purple: #b768aa;
    --purple-veil: rgba(183, 104, 170, 0.9);
    --ink: #1a1016;
    --plum: #6e3f6c;
    --blush: #fbe3f0;
    --bullet: #e0345c;
    --white: #ffffff;
  }
  * { margin: 0; padding: 0; box-sizing: border-box; }
  html, body { width: 848px; height: 1200px; overflow: hidden; background: var(--white); }
  .flyer { position: relative; width: 848px; height: 1200px; overflow: hidden; background: var(--white); font-family: "Oswald", sans-serif; }
  .planner-photo { position: absolute; left: 554px; top: 0; width: 294px; height: 1112px;
    background: linear-gradient(160deg, #f2f2f0 0%, #e6e7e6 35%, #d9dadb 60%, #eeeeec 100%); }
  .backdrop { position: absolute; left: 0; top: 0; }
  .brand { position: absolute; left: 48px; top: 120px; width: 260px; text-align: center;
    font-family: "Oswald", sans-serif; font-weight: 400; font-size: 52px; line-height: 1.05; color: var(--pink); text-transform: uppercase; }
  .headline { position: absolute; font-family: "Cinzel", serif; font-weight: 700; color: var(--ink); font-size: 36px; white-space: nowrap; }
  .headline.line-1 { left: 458px; top: 140px; }
  .headline.line-2 { left: 354px; top: 204px; }
  .headline.line-3 { left: 462px; top: 266px; }
  .headline-note { position: absolute; right: 20px; top: 322px; font-family: "Cousine", monospace; font-weight: 700; font-size: 18px; color: var(--ink); }
  .founder-box { position: absolute; left: 96px; top: 374px; width: 668px; height: 247px; background: var(--purple-veil); text-align: center; }
  .founder { margin-top: 34px; font-family: "Bebas Neue", sans-serif; font-size: 46px; color: var(--ink); line-height: 1; }
  .program-name { font-family: "Oswald", sans-serif; font-weight: 300; font-size: 32px; color: var(--ink); line-height: 1.3; text-transform: uppercase; }
  .mission { margin-top: 14px; font-family: "Cookie", cursive; font-size: 42px; line-height: 1.05; color: var(--blush); }
  .offer-title { position: absolute; left: 58px; top: 656px; font-family: "Montserrat", sans-serif; font-weight: 700; font-size: 24px; color: var(--plum); }
  .offer-list { position: absolute; left: 30px; top: 714px; list-style: none; font-family: "Sofia", cursive; font-size: 24px; color: var(--ink); }
  .offer-list li { position: relative; padding-left: 32px; margin-bottom: 14px; line-height: 1.3; }
  .offer-list li::before { content: ""; position: absolute; left: 2px; top: 11px; border-left: 7px solid var(--bullet); border-top: 5px solid transparent; border-bottom: 5px solid transparent; }
  .hours { position: absolute; text-align: center; font-family: "Sriracha", cursive; color: var(--ink); white-space: nowrap; }
  .hours.main { left: 0; width: 876px; top: 1030px; font-size: 31px; }
  .hours.times { left: 0; width: 812px; top: 1074px; font-size: 25px; }
  .footer-left { position: absolute; left: 0; top: 1120px; width: 554px; height: 80px; background: var(--purple); color: var(--white); }
  .footer-left .icon { position: absolute; }
  .address { position: absolute; left: 50px; top: 10px; font-size: 22px; font-weight: 300; line-height: 1.2; }
  .address small { display: block; font-size: 13px; padding-left: 16px; }
  .call { position: absolute; left: 364px; top: 18px; font-size: 22px; font-weight: 300; }
  .call strong { font-weight: 400; font-size: 24px; }
  .footer-right { position: absolute; right: 18px; top: 1118px; text-align: right; font-family: "Oswald", sans-serif; color: var(--ink); font-size: 17px; line-height: 1.5; }
  .footer-right .label { display: inline-flex; align-items: center; gap: 6px; }
  .footer-right .fb { font-weight: 400; display: inline-flex; align-items: center; gap: 8px; }
  .fb-square { display: inline-block; width: 14px; height: 14px; background: #3b5ea8; }
</style>
</head>
<body>
<main class="flyer">
  <div class="planner-photo" role="img" aria-label="Photo of an open spiral month planner with striped pages"></div>

  <svg class="backdrop" width="848" height="1120" viewBox="0 0 848 1120" aria-hidden="true">
    <polygon points="554,0 554,1120 0,1120 0,346 332,346 332,264 240,196" fill="var(--pink)"/>
    <rect x="554" y="132" width="220" height="56" fill="var(--pink)"/>
    <rect x="554" y="196" width="274" height="56" fill="var(--pink)"/>
    <rect x="554" y="260" width="184" height="52" fill="var(--pink)"/>
  </svg>

  <div class="brand">Ridge<br>Lass<br>Crew</div>

  <h1 class="headline line-1">A Girls Only</h1>
  <p class="headline line-2">After School Program</p>
  <p class="headline line-3">For 11-14yrs</p>
  <p class="headline-note">as OSHC is no longer available</p>

  <section class="founder-box">
    <h2 class="founder">The Brainchild of Rebecca Folwin</h2>
    <p class="program-name">Ridge Lass Crew</p>
    <p class="mission">Dedicated to Coaching &amp; Mentoring Our Girls<br>into Strong, Independent Young women</p>
  </section>

  <h3 class="offer-title">WHAT WE OFFER</h3>
  <ul class="offer-list">
    <li>Daily meditation</li>
    <li>Healthy snacks</li>
    <li>Organised group activity,<br>&nbsp;(yoga, fitness class, soccer etc.)</li>
    <li>Regular guests speakers</li>
    <li>Dedicated homework time</li>
    <li>Social media free zone</li>
  </ul>

  <p class="hours main">Open every afternoon &amp; during school holidays</p>
  <p class="hours times">3-6pm Monday to Friday</p>

  <footer class="footer-left">
    <svg class="icon" style="left:18px;top:20px" width="20" height="28" viewBox="0 0 20 28" aria-hidden="true">
      <path d="M10 1a8 8 0 0 0-8 8c0 6 8 17 8 17s8-11 8-17a8 8 0 0 0-8-8z" fill="none" stroke="#fff" stroke-width="1.5"/>
      <circle cx="10" cy="9" r="3" fill="none" stroke="#fff" stroke-width="1.5"/>
    </svg>
    <p class="address">87 Pelham Pde, Ashvale Heights<small>(across from Crestmoor Day Clinic)</small></p>
    <svg class="icon" style="left:326px;top:24px" width="28" height="26" viewBox="0 0 28 26" aria-hidden="true">
      <path d="M6 3l4 5-2 3c1 3 4 6 7 7l3-2 5 4-3 4C11 23 3 15 2 6z" fill="none" stroke="#fff" stroke-width="1.5" stroke-linejoin="round"/>
      <path d="M17 3a7 7 0 0 1 7 7M17 7a3 3 0 0 1 3 3" fill="none" stroke="#fff" stroke-width="1.3"/>
    </svg>
    <p class="call">Call: <strong>0455817396</strong></p>
  </footer>

  <div class="footer-right">
    <span class="label">e-Mail us
      <svg width="22" height="18" viewBox="0 0 22 18" aria-hidden="true"><rect x="1" y="1" width="20" height="16" fill="none" stroke="#1a1016" stroke-width="1.4"/><path d="M1 1l10 9 10-9" fill="none" stroke="#1a1016" stroke-width="1.4"/></svg>
    </span><br>
    <span>info@ridgelasscrew.example.au</span><br>
    <span class="fb">http://fb.example/ridgelasscrew <span class="fb-square"></span></span>
  </div>
</main>
</body>
</html>
```